Mosquito Outdoor pest control

The uploaded logo must be integrated as the main theme of the card. I would like it to be modern and eye catching. Maybe some backround images or light silver metallic background.
Space enough at the base for contact info to be put in- phone numbers,emails,names,website.
Space on the back for short blog and lines for hand writing..calling card.
Commercial- golf courses, schools, outdoor function properties, pre event treatments.
Residential- retirement villages, townhome complexes and general houses
Management

```html
<!DOCTYPE html>
<html lang="en">
<head>
<meta charset="utf-8">
<title>Bayline Pest Co – Business Card</title>
<link href="https://fonts.googleapis.com/css2?family=Libre+Baskerville:wght@700&family=Open+Sans:wght@400&display=swap" rel="stylesheet">
<style>
  :root{
    --page:#e6e3de;
    --card:#f7f7f6;
    --red:#d71f2b;
    --ink:#111111;
    --text:#2a2a2a;
    --rule:#3a3a3a;
  }
  html,body{margin:0;padding:0;width:1200px;height:902px;overflow:hidden;background:var(--page);}
  .canvas{position:relative;width:1200px;height:902px;}
  .card{position:absolute;top:296px;width:540px;height:309px;background:var(--card);overflow:hidden;box-shadow:0 6px 18px rgba(0,0,0,.18);}
  .card--back{left:40px;}
  .card--front{left:620px;}

  /* back */
  .service-group{position:absolute;left:44px;}
  .service-group--commercial{top:34px;}
  .service-group--residential{top:170px;}
  .service-heading{display:flex;align-items:center;gap:10px;margin:0;font-family:"Libre Baskerville",serif;font-weight:700;font-size:22px;color:var(--red);border-bottom:1px solid var(--red);padding-bottom:3px;width:300px;}
  .service-heading .marker{width:10px;height:10px;background:var(--red);display:inline-block;}
  .service-list{list-style:none;margin:6px 0 0 20px;padding:0;font-family:"Open Sans",sans-serif;font-size:15px;line-height:21px;color:var(--text);}

  /* front */
  .swoosh{position:absolute;left:0;top:0;}
  .brand{position:absolute;left:32px;top:38px;}
  .brand-name{display:flex;align-items:center;gap:12px;font-family:"Libre Baskerville",serif;font-weight:700;font-size:32px;line-height:1;color:var(--ink);}
  .brand-mark{width:14px;height:14px;background:var(--red);flex:none;}
  .brand-tagline{font-family:"Open Sans",sans-serif;font-size:14px;color:var(--text);margin:10px 0 0 26px;}
  .person{position:absolute;left:34px;top:202px;font-family:"Libre Baskerville",serif;font-weight:700;font-size:27px;color:var(--red);}
  .divider{position:absolute;left:268px;top:112px;width:1px;height:106px;background:var(--rule);}
  .contacts{position:absolute;left:286px;top:114px;list-style:none;margin:0;padding:0;font-family:"Open Sans",sans-serif;font-size:13px;color:var(--text);}
  .contacts li{display:flex;align-items:center;gap:9px;height:26px;}
  .contacts svg{flex:none;}
</style>
</head>
<body>
<div class="canvas">

  <section class="card card--back" aria-label="Card back: services">
    <div class="service-group service-group--commercial">
      <h2 class="service-heading"><span class="marker"></span>Commercial</h2>
      <ul class="service-list">
        <li>schools</li>
        <li>golf courses</li>
        <li>pre event treatments</li>
        <li>outdoor function properties</li>
      </ul>
    </div>
    <div class="service-group service-group--residential">
      <h2 class="service-heading"><span class="marker"></span>Residential</h2>
      <ul class="service-list">
        <li>retirement villages</li>
        <li>townhome complexes</li>
        <li>general houses</li>
      </ul>
    </div>
  </section>

  <section class="card card--front" aria-label="Card front">
    <svg class="swoosh" width="540" height="309" viewBox="0 0 540 309" aria-hidden="true">
      <path d="M0,309 C200,292 420,252 540,204 L540,309 Z" fill="var(--ink)"/>
      <path d="M40,309 C220,272 430,224 540,172 L540,188 C430,238 230,288 40,309 Z" fill="var(--red)"/>
    </svg>

    <div class="brand">
      <div class="brand-name"><span class="brand-mark"></span>Bayline Pest Co</div>
      <div class="brand-tagline">Outdoor pest control</div>
    </div>

    <div class="person">Sam Carter</div>
    <div class="divider"></div>

    <ul class="contacts">
      <li>
        <svg width="14" height="14" viewBox="0 0 14 14" aria-hidden="true"><rect width="14" height="14" fill="var(--red)"/><path d="M4 3 L6 3 L6.5 5.5 L5.5 6.3 Q6.3 8 7.8 8.6 L8.6 7.6 L11 8.2 L11 10.3 Q6 10.5 3.8 5.5 Z" fill="#fff"/></svg>
        061 2043 7795
      </li>
      <li>
        <svg width="14" height="14" viewBox="0 0 14 14" aria-hidden="true"><rect width="14" height="14" fill="var(--red)"/><circle cx="7" cy="7" r="4" fill="none" stroke="#fff" stroke-width="1.2"/><path d="M3 7 H11 M7 3 V11" stroke="#fff" stroke-width="1"/></svg>
        www.baylinepest.com
      </li>
      <li>
        <svg width="14" height="14" viewBox="0 0 14 14" aria-hidden="true"><rect width="14" height="14" fill="var(--red)"/><rect x="3" y="4.5" width="8" height="5.5" fill="none" stroke="#fff" stroke-width="1"/><path d="M3 4.5 L7 7.8 L11 4.5" fill="none" stroke="#fff" stroke-width="1"/></svg>
        hello@baylinepest.com
      </li>
    </ul>
  </section>

</div>
</body>
</html>
```